Business Card Design

My business is writing crime novels to entertain readers. I write legal thrillers and mysteries. I need a card for publishers, agents, other authors, and media.

Industry/Entity Type

Legal

Contact Information for Business Card

Paul Derrow
www.derrowfiction.example
pauljderrow@inkpost.example
0064 27 5190472

```html
<!DOCTYPE html>
<html lang="en">
<head>
<meta charset="utf-8">
<title>Paul Derrow — Business Card</title>
<link rel="stylesheet" href="https://fonts.googleapis.com/css2?family=Kalam:wght@400;700&display=swap">
<style>
  :root {
    --page-bg: #e9e4d8;
    --card-black: #000000;
    --red-glow: #ff1414;
    --red-mid: #c40000;
    --red-deep: #7a0000;
    --red-edge: #560000;
    --divider: #ffffff;
    --text-light: #ffffff;
    --portrait-tone: #2a2a2a;
  }
  * { box-sizing: border-box; margin: 0; padding: 0; }
  html, body {
    width: 1200px;
    height: 729px;
    overflow: hidden;
  }
  body {
    background: var(--page-bg);
    position: relative;
    font-family: "Kalam", cursive;
  }
  .business-card {
    position: absolute;
    left: 220px;
    top: 150px;
    width: 760px;
    height: 430px;
    border-radius: 26px;
    overflow: hidden;
    display: flex;
    box-shadow: 0 8px 22px rgba(0, 0, 0, 0.35);
  }
  .portrait-area {
    width: 300px;
    height: 100%;
    background: radial-gradient(ellipse at 45% 70%, var(--portrait-tone) 0%, var(--card-black) 70%);
  }
  .card-divider {
    width: 2px;
    height: 100%;
    background: var(--divider);
  }
  .info-panel {
    flex: 1;
    position: relative;
    background: radial-gradient(circle at 48% 38%, var(--red-glow) 0%, var(--red-mid) 28%, var(--red-deep) 62%, var(--red-edge) 100%);
    color: var(--text-light);
    padding: 110px 0 0 78px;
  }
  .author-name {
    font-size: 48px;
    font-weight: 700;
    letter-spacing: 1px;
    line-height: 1;
    margin-bottom: 38px;
  }
  .contact-list {
    list-style: none;
    padding-left: 26px;
  }
  .contact-item {
    display: flex;
    align-items: center;
    gap: 14px;
    font-size: 22px;
    line-height: 1.5;
  }
  .contact-icon {
    width: 20px;
    height: 20px;
    flex: none;
  }
</style>
</head>
<body>
  <div class="business-card">
    <div class="portrait-area" role="img" aria-label="Portrait photograph of the author in a dark jacket and white shirt against a black background"></div>
    <div class="card-divider"></div>
    <div class="info-panel">
      <h1 class="author-name">Paul Derrow</h1>
      <ul class="contact-list">
        <li class="contact-item">
          <svg class="contact-icon" viewBox="0 0 20 20" aria-hidden="true">
            <path d="M3 6 Q10 1 17 6 L15 9 L13 8 L13 6.5 Q10 5.5 7 6.5 L7 8 L5 9 Z" fill="#fff"/>
            <rect x="5" y="10" width="10" height="7" rx="1.5" fill="#fff"/>
            <circle cx="10" cy="13.5" r="1.8" fill="#a00000"/>
          </svg>
          <span>0064 27 5190472</span>
        </li>
        <li class="contact-item">
          <svg class="contact-icon" viewBox="0 0 20 20" aria-hidden="true">
            <rect x="2" y="5" width="16" height="11" rx="1" fill="#fff"/>
            <path d="M2.5 5.5 L10 11 L17.5 5.5" fill="none" stroke="#a00000" stroke-width="1.4"/>
          </svg>
          <span>pauljderrow@inkpost.example</span>
        </li>
        <li class="contact-item">
          <svg class="contact-icon" viewBox="0 0 20 20" aria-hidden="true">
            <circle cx="10" cy="10" r="7.5" fill="none" stroke="#fff" stroke-width="1.6"/>
            <ellipse cx="10" cy="10" rx="3.2" ry="7.5" fill="none" stroke="#fff" stroke-width="1.3"/>
            <line x1="2.5" y1="10" x2="17.5" y2="10" stroke="#fff" stroke-width="1.3"/>
          </svg>
          <span>www.derrowfiction.example</span>
        </li>
      </ul>
    </div>
  </div>
</body>
</html>
```